RW Holloway LLC Business Card - Civil Engineering & Consulting Firm

We need a Business Card that is elegant, and masculine.  It is our Professional Civil Engineering & Consulting Company located in San Antonio TX (Not s construction or builder firm- no gears & no tool images please). We provide civil engineering services including  commercial site plans, grading and drainage plans, utility plans, hydraulics and hydrology, land planning, utility coordination, and other general civil engineering services related to commercial and residential development.
We have 2 existing Logos. We would like to convey reliability, strength, trustworthiness and attention to detail.  Blues and orange tones as per logo We are OK with the use of a darker blue in the mix.  We have 2 logo versions - Full Company Name Logo to go on the back of card, & Small Icon Logo for the front w/ personal Info.

Target Market(s)
Architects, Real Estate Developers, Other Strctural Engineers, Surveyers, General Contractors
Industry/Entity Type
Professional Civil Engineering
Contact Information for Business Card
Name, Position, Address, Cell & Office #, email, and company website
Font styles to use
Other font styles liked:
- Avian
Requirements
Should not have
- No Tools, No Gears, no Cranes, or Construction Equipment.

```html
<!DOCTYPE html>
<html lang="en">
<head>
<meta charset="utf-8">
<title>RW Holloway LLC – Business Card</title>
<link rel="stylesheet" href="https://fonts.googleapis.com/css2?family=Arimo:wght@400;700&family=Questrial&display=swap">
<style>
  :root{
    --bg:#c9c9c9;
    --card-dark:#2b2b2b;
    --sky:#7badda;
    --sky-deep:#6b9fcf;
    --orange:#f29a2e;
    --white:#ffffff;
    --grey-text:#d8d8d8;
  }
  *{margin:0;padding:0;box-sizing:border-box}
  html,body{width:1200px;height:800px;overflow:hidden}
  body{
    background:var(--bg);
    display:flex;align-items:center;justify-content:center;gap:40px;
    font-family:"Arimo",Arial,sans-serif;
  }
  .card{
    width:540px;height:310px;position:relative;overflow:hidden;
    box-shadow:0 8px 22px rgba(0,0,0,.25);
  }
  /* front */
  .card--front{background:var(--card-dark);border-bottom:3px solid var(--sky)}
  .brand{
    position:absolute;left:40px;top:118px;
    display:flex;align-items:center;gap:10px;
  }
  .brand__square{width:14px;height:14px;background:var(--orange)}
  .brand__name{color:var(--orange);font-size:22px;font-weight:400;letter-spacing:1px}
  .divider{position:absolute;left:262px;top:36px;width:1px;height:150px;background:var(--sky)}
  .contact{position:absolute;left:286px;top:36px;color:var(--grey-text);font-size:12.5px;line-height:1.45}
  .contact__name{font-family:"Questrial",sans-serif;font-size:20px;letter-spacing:1px;color:var(--sky)}
  .contact__name span{color:var(--orange)}
  .contact__role{font-size:13px;margin-bottom:10px}
  .contact__row{display:flex;align-items:center;gap:7px}
  .contact__row svg{width:12px;height:12px;flex:none}
  .accent{color:var(--orange)}
  .contact__address{margin-top:10px}
  .tagline{
    position:absolute;left:40px;right:40px;bottom:28px;
    color:var(--white);font-size:14px;letter-spacing:.5px;text-align:right;
  }
  /* back */
  .card--back{background:var(--sky)}
  .back__pattern{position:absolute;inset:0;width:100%;height:100%}
  .back__brand{
    position:absolute;inset:0;display:flex;align-items:center;justify-content:center;gap:12px;
  }
  .back__square{width:18px;height:18px;background:var(--white)}
  .back__name{color:var(--white);font-size:30px;font-weight:400;letter-spacing:2px}
</style>
</head>
<body>
  <section class="card card--front">
    <div class="brand">
      <span class="brand__square"></span>
      <span class="brand__name">RW Holloway LLC</span>
    </div>
    <div class="divider"></div>
    <div class="contact">
      <p class="contact__name">DANIEL <span>REYES</span></p>
      <p class="contact__role">Managing Director</p>
      <p class="contact__row">
        <svg viewBox="0 0 12 12"><path d="M3 1l2 2.5-1.2 1.2a6 6 0 0 0 3.5 3.5L8.5 7 11 9l-1.3 1.8C5.5 10.5 1.5 6.5 1.2 2.3z" fill="var(--sky)"/></svg>
        044-555 010 234
      </p>
      <p class="contact__row">
        <svg viewBox="0 0 12 12"><rect x="1" y="2.5" width="10" height="7" fill="var(--sky)"/><path d="M1 2.5l5 4 5-4" stroke="var(--card-dark)" fill="none"/></svg>
        info@hollowayce.com
      </p>
      <p class="contact__row">
        <svg viewBox="0 0 12 12"><circle cx="6" cy="6" r="5" fill="var(--sky)"/><path d="M1 6h10M6 1c-2.5 3-2.5 7 0 10M6 1c2.5 3 2.5 7 0 10" stroke="var(--card-dark)" stroke-width=".8" fill="none"/></svg>
        www.<span class="accent">hollowayce</span>.com
      </p>
      <p class="contact__address">218, Alamo Ridge Drive<br>78205, San Antonio TX</p>
    </div>
    <p class="tagline">COMMERCIAL AND RESIDENTIAL DEVELOPMENT</p>
  </section>

  <section class="card card--back">
    <svg class="back__pattern" role="img" aria-label="Embossed repeating pattern of the company icon" viewBox="0 0 540 310" preserveAspectRatio="none">
      <defs>
        <linearGradient id="emboss" x1="0" y1="0" x2="1" y2="1">
          <stop offset="0" stop-color="#80b2de"/>
          <stop offset="1" stop-color="#74a8d6"/>
        </linearGradient>
      </defs>
      <rect width="540" height="310" fill="url(#emboss)"/>
    </svg>
    <div class="back__brand">
      <span class="back__square"></span>
      <span class="back__name">RW Holloway LLC</span>
    </div>
  </section>
</body>
</html>
```